Online Training company needs a new website design (Wordpress)

We are looking for a new design for our website (run on WordPress). We currently have two websites (quizbrightly.com) and (velmoracademy.com) and are trying to combine them into a single design.

The site should contain the following sections (Start Here, courses, labs, practice exams, exam vouchers, books, articles, about us).

Start Here - With so many options on our site, we think it would be a good idea to have this page that will allow us to give students an overview of our different products/services and where to start when they first find out about our company.

Courses - These are our online video courses (products), currently hosted at velmoracademy.com. Each course has its own "product page".

Labs - These are online lab environments that a student can purchase. The layout for these would be similar to a course, but the purchase option will be different (our web developer will code all the back end stuff to make it work).

Practice Exams - This will allow students to take practice questions to study for their exams.

Exam Vouchers - Students can purchase their exam vouchers here at a discounted price for their certification exams.

Books - Will link to a page that displays our books that are available on Brixly. (Examples of the covers are attached so you can see our current designs.)

Articles - This will be our "blog" area for us to post articles each week.

About Us - A short about us page describing our company.

***
As for the design of the page itself, we like the current color scheme at velmoracademy.com, but the layout isn't working well. It was fine when we just had video courses, but as we have added new products it is becoming more and more cumbersome.

I have been looking for inspiration around the web, and saw quietharvestplan.com as a good example of trying to provide focus to new users, while breaking out various parts of a business that contains 4-6 different product lines/topics. Another example of a site we like is lessonlanternhub.com.

That said, we aren't looking to simply copy either site, and are completely open to recommendations and designs you may have.

Thank you and we look forward to working with you!

```html
<!DOCTYPE html>
<html lang="en">
<head>
<meta charset="utf-8">
<title>Quiz Brightly — Online Training</title>
<link href="https://fonts.googleapis.com/css2?family=Poppins:wght@400;500;600&family=Quicksand:wght@400;500;600&display=swap" rel="stylesheet">
<style>
:root{
  --brand:#3f6fa1;
  --brand-dark:#355f8c;
  --heading:#3b74ab;
  --ink:#222;
  --muted:#666;
  --light:#f4f4f4;
  --line:#d9dde3;
  --white:#fff;
}
*{box-sizing:border-box;margin:0;padding:0}
html,body{width:1200px;height:4390px;overflow:hidden}
body{font-family:"Quicksand",sans-serif;color:var(--ink);background:var(--white);position:relative}
h1,h2,h3,h4{font-family:"Poppins",sans-serif;font-weight:500}
a{color:inherit;text-decoration:none}
.section{position:absolute;left:0;width:1200px}
.section-title{color:var(--heading);font-size:29px;text-align:center}
.btn{display:inline-block;font-family:"Poppins",sans-serif;font-size:16px;padding:0 26px;line-height:42px;border:2px solid var(--brand);color:var(--brand);background:#fff}
.btn--solid{background:var(--brand);color:#fff}

/* top bar */
.topbar{top:0;height:32px;background:var(--brand);color:#fff;font-size:14px}
.topbar .contact{position:absolute;left:79px;top:7px;display:flex;gap:38px;align-items:center}
.topbar .contact span{display:flex;gap:10px;align-items:center}
.topbar .social{position:absolute;right:70px;top:10px;display:flex;gap:16px}
.topbar .social i{width:12px;height:12px;border-radius:50%;background:#fff;display:block}

/* nav */
.nav{top:32px;height:108px;background:#fff;border-bottom:1px solid #eee}
.logo{position:absolute;left:79px;top:32px;display:flex;align-items:center;gap:12px;font-family:"Poppins",sans-serif;font-weight:600;font-size:24px;color:var(--brand)}
.logo i{width:40px;height:40px;border-radius:50%;background:var(--brand);display:block}
.menu{position:absolute;left:302px;top:44px;display:flex;gap:40px;font-size:16px;color:#333}
.menu .active{color:var(--brand);font-weight:600;position:relative}
.menu .active::after{content:"";position:absolute;left:50%;margin-left:-10px;top:28px;width:20px;height:3px;background:var(--brand)}
.nav .btn{position:absolute;right:78px;top:34px;line-height:40px;padding:0 28px}

/* hero */
.hero{top:140px;height:548px;background:var(--light)}
.hero h1{position:absolute;left:79px;top:198px;width:420px;font-size:30px;line-height:40px;color:var(--heading)}
.hero .actions{position:absolute;left:79px;top:308px;display:flex;gap:18px}
.hero .actions .btn{line-height:36px;padding:0 28px}
.hero-image{position:absolute;left:520px;top:0;width:680px;height:548px;background:linear-gradient(135deg,#f2f2f2 0%,#e3e4e6 45%,#cfd6cf 75%,#ececec 100%)}
.dots{position:absolute;display:flex;gap:9px}
.dots i{width:11px;height:11px;border:1.5px solid var(--brand);border-radius:50%;display:block}
.dots i.on{background:var(--brand)}

/* insider */
.insider{top:688px;height:424px;text-align:center}
.insider h2{margin-top:62px}
.insider p{font-size:15px;color:var(--muted);line-height:26px;width:760px;margin:0 auto}
.insider .lead{margin-top:26px}
.subscribe{width:450px;margin:34px auto 0;border-bottom:1px solid #c8c8c8;display:flex;justify-content:space-between;padding:0 14px 12px;font-size:14px;color:#999}
.insider .note{margin-top:42px}

/* welcome */
.welcome{top:1112px;height:418px;background:var(--light)}
.welcome-image{position:absolute;left:0;top:0;width:483px;height:418px;background:linear-gradient(120deg,#cfd7e0,#e6e2dc 50%,#b9c6d2)}
.welcome h2{position:absolute;left:548px;top:72px;font-size:27px;color:var(--heading)}
.welcome p{position:absolute;left:548px;top:128px;width:560px;font-size:15px;line-height:26px;color:#444}
.welcome .btn{position:absolute;left:548px;top:316px;line-height:40px;padding:0 32px}

/* courses */
.courses{top:1530px;height:695px}
.courses h2{position:absolute;width:100%;top:62px}
.course{position:absolute;background:#fff;border:1px solid #ddd;text-align:center}
.course--featured{box-shadow:0 8px 24px rgba(0,0,0,.25);border-color:#ccc}
.course-image{margin:6px;background:linear-gradient(135deg,#1f2a44,#3a4d7a 60%,#1a2236)}
.course h3{font-family:"Quicksand",sans-serif;font-weight:600;font-size:15px;color:var(--brand);margin-top:18px}
.course p{font-size:13px;color:#555;line-height:20px;margin:8px 22px 0}
.course .price{font-weight:700;color:var(--brand);font-size:15px;margin-top:10px}
.circle-arrow{width:38px;height:38px;border-radius:50%;background:var(--brand-dark);margin:14px auto 0;display:flex;align-items:center;justify-content:center}

/* learn */
.learn{top:2225px;height:395px;background:var(--light)}
.learn h2{position:absolute;width:100%;top:56px}
.ways{position:absolute;top:128px;left:105px;width:990px;display:flex;justify-content:space-between}
.way{width:190px;text-align:center}
.way .icon{width:80px;height:80px;border-radius:50%;background:#dbe4ee;margin:0 auto;display:flex;align-items:center;justify-content:center}
.way .icon span{width:58px;height:58px;border-radius:50%;background:var(--brand);display:flex;align-items:center;justify-content:center}
.way h4{font-size:18px;margin-top:18px;color:#222}
.way p{font-size:14px;line-height:22px;color:#555;margin-top:8px}
.way p a{color:var(--brand);text-decoration:underline}

/* articles */
.articles{top:2620px;height:570px}
.articles h2{position:absolute;left:79px;top:70px;font-size:28px;color:var(--heading)}
.book-cover{position:absolute;left:79px;top:140px;width:243px;height:366px;background:linear-gradient(180deg,#2f5f93 0%,#2f5f93 12%,#f3f5f8 12%,#dce8f3 70%,#2f5f93 88%)}
.article-body{position:absolute;left:372px;top:136px;width:345px}
.article-body h3{font-size:21px;color:#111}
.article-body .author{font-size:14px;margin-top:16px;color:#333}
.article-body p{font-size:14px;line-height:23px;color:#444;margin-top:18px}
.article-body .link{display:block;margin-top:20px;font-size:14px;line-height:22px;color:var(--brand);text-decoration:underline}
.person-image{position:absolute;left:746px;top:44px;width:454px;height:526px;background:linear-gradient(180deg,#ffffff 0%,#eef2f6 40%,#a9c6e4 100%)}

/* news */
.news{top:3190px;height:470px;background:#fafafa}
.news h2{position:absolute;width:100%;top:56px}
.post{position:absolute;top:123px;width:325px}
.post-image{height:205px;background:linear-gradient(135deg,#d8d2c8,#b7b9bd 55%,#7f8895)}
.post h3{font-family:"Quicksand",sans-serif;font-weight:700;font-size:15px;color:var(--brand);margin-top:12px}
.post .meta{display:flex;justify-content:space-between;font-size:13px;color:#999;margin-top:8px}
.post .meta .more{color:var(--brand);display:flex;gap:8px;align-items:center}

/* contact */
.contact-sec{top:3660px;height:555px;text-align:center}
.contact-sec h2{margin-top:60px}
.contact-sec .intro{font-size:15px;color:#444;line-height:25px;width:700px;margin:28px auto 0}
.form{position:absolute;left:401px;top:212px;width:398px}
.field{height:44px;border:1px solid var(--line);margin-bottom:12px;text-align:left;padding:12px 10px;font-size:13px;color:#aaa}
.field.focus{border:2px solid var(--brand);color:var(--brand)}
.field.msg{height:80px}
.form .btn{margin-top:1px;line-height:40px;padding:0 36px;font-size:15px}

/* footer */
.footer{top:4215px;height:175px;background:var(--brand);color:#fff}
.partners{position:absolute;top:52px;width:100%;display:flex;justify-content:center;gap:66px;font-family:"Poppins",sans-serif;font-size:19px;font-weight:500}
.footer .bar{position:absolute;top:124px;left:0;width:100%;border-top:1px solid rgba(255,255,255,.3)}
.footer .copy{position:absolute;left:79px;top:142px;font-size:14px;font-weight:600}
.footer .social{position:absolute;right:70px;top:146px;display:flex;gap:16px}
.footer .social i{width:12px;height:12px;border-radius:50%;background:#fff;display:block}
</style>
</head>
<body>

<header class="section topbar">
  <div class="contact">
    <span><svg width="16" height="12" viewBox="0 0 16 12"><rect x="0.5" y="0.5" width="15" height="11" fill="none" stroke="#fff"/><path d="M1 1l7 6 7-6" fill="none" stroke="#fff"/></svg>info@quizbrightly.com</span>
    <span><svg width="14" height="14" viewBox="0 0 14 14"><path d="M3 1l2.5 3-1.5 2a8 8 0 004 4l2-1.5 3 2.5-1.5 2.5C6 13 1 8 0.5 2.5z" fill="#fff"/></svg>123 456 7890</span>
  </div>
  <div class="social"><i></i><i></i><i></i></div>
</header>

<nav class="section nav">
  <div class="logo"><i></i>Quiz Brightly</div>
  <div class="menu">
    <a class="active">About Us</a><a>Courses</a><a>Labs</a><a>Practice Exams</a><a>Exam Vouchers</a><a>Books</a><a>Articles</a>
  </div>
  <a class="btn btn--solid">Start Here</a>
</nav>

<section class="section hero">
  <h1>Learn the information. Pass the certification.</h1>
  <div class="actions"><a class="btn">Know More</a><a class="btn btn--solid">Get Free ebook</a></div>
  <div class="hero-image" role="img" aria-label="Student working on a laptop at a desk with plants and floating line icons"></div>
  <div class="dots" style="left:79px;top:474px"><i class="on"></i><i></i><i></i></div>
</section>

<section class="section insider">
  <h2 class="section-title">Become A Quiz Brightly Insider</h2>
  <p class="lead">Join thousands of students who received our FREE eBook of SVCM v3 Foundations (Quiz Brightly) delivered right to your inbox and an exclusive special price on our video course!</p>
  <div class="subscribe"><span>Enter e-mail*</span><svg width="18" height="16" viewBox="0 0 18 16"><path d="M0 7L18 0 13 16 9 10z" fill="var(--brand)"/></svg></div>
  <p class="note">By subscribing to QUIZ BRIGHTLY Insider, you will receive a free eBook sample version of the SVCM v3 Foundations (Quiz Brightly) book with over 50 pages of excellent content including a free full practice test.</p>
</section>

<section class="section welcome">
  <div class="welcome-image" role="img" aria-label="Three students studying together at laptops"></div>
  <h2>Welcome To Quiz Brightly</h2>
  <p>Marcus Ellery is an assistant professor and instructor at multiple universities and colleges. He has trained thousands of students across the globe in his cyber security and information technology courses. He holds numerous information technology professional certifications including Certified Systems Assurance Professional (CSAP), Certified Ethical Analyst (CEA), Certified Network Defense Specialist (CNDS), Digital Forensic Examiner (DFX).</p>
  <a class="btn btn--solid">Learn More</a>
</section>

<section class="section courses">
  <h2 class="section-title">Our Cources</h2>
  <article class="course" style="left:79px;top:138px;width:304px;height:380px">
    <div class="course-image" style="height:182px;background:linear-gradient(135deg,#c9d2f0,#8f9fd6 60%,#c9d2f0)" role="img" aria-label="Collage of certification badges with Full Access label"></div>
    <h3>Full Access to All Our Courses</h3>
    <p>With our $9/month plan, you</p>
    <div class="price">$9 / month</div>
    <div class="circle-arrow"><svg width="14" height="12" viewBox="0 0 14 12"><path d="M0 6h12M7 1l5 5-5 5" stroke="#fff" stroke-width="2" fill="none"/></svg></div>
  </article>
  <article class="course course--featured" style="left:430px;top:125px;width:337px;height:420px">
    <div class="course-image" style="height:208px" role="img" aria-label="Dark course cover for the SVCM Foundation voucher"></div>
    <h3>SVCM Foundation (Exam Voucher)</h3>
    <p>Purchase your discounted SVCM Foundation exam voucher directly from Velmor Academy</p>
    <div class="price">$299</div>
    <div class="circle-arrow"><svg width="14" height="12" viewBox="0 0 14 12"><path d="M0 6h12M7 1l5 5-5 5" stroke="#fff" stroke-width="2" fill="none"/></svg></div>
  </article>
  <article class="course" style="left:817px;top:138px;width:304px;height:380px">
    <div class="course-image" style="height:182px;background:linear-gradient(135deg,#1d3a63,#3b6aa5 60%,#1d3a63)" role="img" aria-label="Blue course cover for the PROJEX Foundation voucher"></div>
    <h3>PROJEX Foundation (Exam Voucher)</h3>
    <p>Purchase your discounted PROJEX foundation exam voucher directly from Velmor Academy</p>
    <div class="price">$299</div>
    <div class="circle-arrow"><svg width="14" height="12" viewBox="0 0 14 12"><path d="M0 6h12M7 1l5 5-5 5" stroke="#fff" stroke-width="2" fill="none"/></svg></div>
  </article>
  <div class="dots" style="left:517px;top:606px;align-items:center">
    <svg width="18" height="18" viewBox="0 0 18 18"><circle cx="9" cy="9" r="8" fill="none" stroke="var(--brand)"/><path d="M10.5 5L6.5 9l4 4" stroke="var(--brand)" fill="none"/></svg>
    <i class="on" style="width:8px;height:8px"></i><i style="width:8px;height:8px;border-color:#aaa"></i><i style="width:8px;height:8px;border-color:#aaa"></i><i style="width:8px;height:8px;border-color:#aaa"></i><i style="width:8px;height:8px;border-color:#aaa"></i>
    <svg width="18" height="18" viewBox="0 0 18 18"><circle cx="9" cy="9" r="8" fill="none" stroke="var(--brand)"/><path d="M7.5 5l4 4-4 4" stroke="var(--brand)" fill="none"/></svg>
  </div>
</section>

<section class="section learn">
  <h2 class="section-title">How you can learn with us</h2>
  <div class="ways">
    <div class="way">
      <div class="icon"><span><svg width="26" height="26" viewBox="0 0 26 26"><circle cx="13" cy="13" r="11" fill="none" stroke="#fff" stroke-width="2"/><path d="M10 8l8 5-8 5z" fill="#fff"/></svg></span></div>
      <h4>Videos</h4>
      <p>Using our Quiz Brightly video series, we take complicated certification...<a>Read More</a></p>
    </div>
    <div class="way">
      <div class="icon"><span><svg width="26" height="22" viewBox="0 0 26 22"><path d="M1 2h9a3 3 0 013 3v16a3 3 0 00-3-3H1zM25 2h-9a3 3 0 00-3 3v16a3 3 0 013-3h9z" fill="none" stroke="#fff" stroke-width="2"/></svg></span></div>
      <h4>Books</h4>
      <p>Our Quiz Brightly book series will get you certified in the shortest amount...<a>Read More</a></p>
    </div>
    <div class="way">
      <div class="icon"><span><svg width="24" height="24" viewBox="0 0 24 24" fill="#fff"><rect x="1" y="1" width="9" height="9" rx="2"/><rect x="14" y="1" width="9" height="9" rx="2"/><rect x="1" y="14" width="9" height="9" rx="2"/><rect x="14" y="14" width="9" height="9" rx="2"/></svg></span></div>
      <h4>Apps</h4>
      <p>Our quiz apps prepare you for the certification exam while on the go!...<a>Read More</a></p>
    </div>
    <div class="way">
      <div class="icon"><span><svg width="22" height="26" viewBox="0 0 22 26"><path d="M1 1h14l6 6v18H1z" fill="none" stroke="#fff" stroke-width="2"/><path d="M5 12h12M5 16h12M5 20h8" stroke="#fff" stroke-width="2"/></svg></span></div>
      <h4>Blog</h4>
      <p>Signup for your daily dose of training with our constantly updated blog feed...<a>Read More</a></p>
    </div>
  </div>
</section>

<section class="section articles">
  <h2>Get Ready To Pass With Our Latest Articles</h2>
  <div class="book-cover" role="img" aria-label="Book cover for SVCM Foundation by Marcus Ellery with graduation cap artwork"></div>
  <div class="article-body">
    <h3>SVCM<sup style="font-size:11px">®</sup> FOUNDATION</h3>
    <div class="author">- MARCUS ELLERY</div>
    <p>Lorem Ipsum is simply dummy text of the printing and typesetting industry. Lorem Ipsum has been the industry's standard dummy text ever since the 1500s, when an unknown printer took a galley of type and scrambled it to make a type specimen book. It has survived not only five centuries, but also the leap into electronic typesetting, remaining essentially unchanged.</p>
    <a class="link">Now available on Brixly.com in paperback and eBook formats!</a>
  </div>
  <div class="person-image" role="img" aria-label="Smiling student giving two thumbs up"></div>
</section>

<section class="section news">
  <h2 class="section-title">Recent News</h2>
  <article class="post" style="left:79px">
    <div class="post-image" role="img" aria-label="Two people reviewing work on a laptop"></div>
    <h3>Lorem Ipsum is typesetting industry.</h3>
    <div class="meta"><span>💬 Comments</span><span class="more">Learn More <svg width="14" height="10" viewBox="0 0 14 10"><path d="M0 5h12M8 1l4 4-4 4" stroke="var(--brand)" stroke-width="1.5" fill="none"/></svg></span></div>
  </article>
  <article class="post" style="left:438px">
    <div class="post-image" role="img" aria-label="Hands typing on a laptop with a phone on the desk" style="background:linear-gradient(135deg,#c9cdd2,#8c949e 60%,#5c6570)"></div>
    <h3>Lorem Ipsum is typesetting industry.</h3>
    <div class="meta"><span>💬 Comments</span><span class="more">Learn More <svg width="14" height="10" viewBox="0 0 14 10"><path d="M0 5h12M8 1l4 4-4 4" stroke="var(--brand)" stroke-width="1.5" fill="none"/></svg></span></div>
  </article>
  <article class="post" style="left:796px">
    <div class="post-image" role="img" aria-label="Student studying at a laptop in warm light" style="background:linear-gradient(135deg,#f1e7da,#c9a789 55%,#6f5444)"></div>
    <h3>Lorem Ipsum is typesetting industry.</h3>
    <div class="meta"><span>💬 Comments</span><span class="more">Learn More <svg width="14" height="10" viewBox="0 0 14 10"><path d="M0 5h12M8 1l4 4-4 4" stroke="var(--brand)" stroke-width="1.5" fill="none"/></svg></span></div>
  </article>
</section>

<section class="section contact-sec">
  <h2 class="section-title">Contact Us</h2>
  <p class="intro">Lorem Ipsum is simply dummy text of the printing and typesetting industry. Lorem Ipsum has been the industry's standard dummy text ever since the 1500s,</p>
  <form class="form">
    <div class="field focus">Name*</div>
    <div class="field">E-mail*</div>
    <div class="field">Phone*</div>
    <div class="field msg">Message</div>
    <a class="btn btn--solid">Submit</a>
  </form>
</section>

<footer class="section footer">
  <div class="partners"><span>Brixly</span><span>Streamory</span><span>Learnvale</span><span>Linkory Learning</span></div>
  <div class="bar"></div>
  <div class="copy">© QB QUIZ BRIGHTLY - 2018. All Rights Reserved.</div>
  <div class="social"><i></i><i></i><i></i></div>
</footer>

</body>
</html>
```